Redesign of business card for Cedar Ridge Mechanical

We are looking for a new design for our business cards for Cedar Ridge Mechanical. We are a plumbing & HVAC construction company, operating on the West Coast of Canada and USA. Logo attached.
Industry/Entity Type
Construction - Plumbing & HVAC
Contact Information for Business Card
Name, address, phone numbers, email, website address
Look and feel
Each slider illustrates characteristics of the customer's brand and the style your logo design should communicate.

```html
<!DOCTYPE html>
<html lang="en">
<head>
<meta charset="utf-8">
<title>Cedar Ridge Mechanical — Business Card</title>
<link rel="stylesheet" href="https://fonts.googleapis.com/css2?family=Montserrat:wght@400;500;700;800&display=swap">
<style>
  :root {
    --stage: #2a2a2a;
    --card: #141414;
    --ink: #ffffff;
    --muted: #d9d9d9;
    --band: #f2f2f2;
    --band-ink: #6b6b6b;
    --strip: #8a8a8a;
    --pattern-a: #1c1c1c;
    --pattern-b: #242424;
  }
  * { box-sizing: border-box; margin: 0; padding: 0; }
  html, body { width: 1200px; height: 963px; overflow: hidden; }
  body {
    background: var(--stage);
    font-family: "Montserrat", sans-serif;
    color: var(--ink);
    position: relative;
  }
  .card {
    position: absolute;
    left: 280px;
    width: 640px;
    height: 366px;
    background: var(--card);
    border-radius: 18px;
    overflow: hidden;
    box-shadow: 0 14px 40px rgba(0,0,0,.55);
  }
  .card--front { top: 60px; }
  .card--back { top: 520px; }

  /* Front */
  .holder { position: absolute; left: 42px; top: 60px; }
  .holder__name { font-size: 27px; font-weight: 800; letter-spacing: .5px; line-height: 1.2; }
  .holder__title { font-size: 17px; font-weight: 400; color: var(--muted); margin-top: 2px; }

  .brand {
    position: absolute; right: 44px; top: 56px;
    display: flex; align-items: center; gap: 12px;
  }
  .brand__square { width: 26px; height: 26px; background: var(--ink); flex: none; }
  .brand__name {
    font-size: 24px; font-weight: 700; line-height: 1.15;
    text-transform: uppercase; letter-spacing: 1px;
  }

  .rule-main {
    position: absolute; left: 30px; right: 44px; top: 140px;
    height: 1.5px; background: var(--ink);
  }

  .contacts { position: absolute; left: 42px; top: 158px; list-style: none; }
  .contacts li {
    display: flex; align-items: center; gap: 10px;
    font-size: 17px; font-weight: 500; margin-bottom: 8px;
  }
  .contacts svg { width: 16px; height: 16px; fill: var(--ink); flex: none; }

  .address {
    position: absolute; right: 44px; top: 236px;
    width: 220px; text-align: right;
    font-size: 16px; font-weight: 500; line-height: 1.3;
  }

  .band-strip {
    position: absolute; left: 0; bottom: 0; width: 100%; height: 56px;
  }
  .website {
    position: absolute; right: 44px; bottom: 14px;
    font-size: 17px; font-weight: 500; color: var(--band-ink);
  }

  /* Back */
  .back-pattern {
    position: absolute; inset: 0;
    background: repeating-linear-gradient(135deg, var(--pattern-a) 0 22px, var(--pattern-b) 22px 24px);
  }
  .back-brand {
    position: absolute; right: 44px; bottom: 40px;
    display: flex; align-items: center; gap: 10px;
  }
  .back-brand__square { width: 18px; height: 18px; background: var(--ink); }
  .back-brand__name { font-size: 18px; font-weight: 700; text-transform: uppercase; letter-spacing: 1px; }
</style>
</head>
<body>

<section class="card card--front" aria-label="Business card front">
  <div class="holder">
    <h1 class="holder__name">DANIEL HAYES</h1>
    <p class="holder__title">Manager</p>
  </div>

  <div class="brand">
    <span class="brand__square"></span>
    <span class="brand__name">Cedar Ridge<br>Mechanical</span>
  </div>

  <div class="rule-main"></div>

  <ul class="contacts">
    <li>
      <svg viewBox="0 0 24 24" aria-hidden="true"><path d="M6.6 10.8a15.1 15.1 0 0 0 6.6 6.6l2.2-2.2a1 1 0 0 1 1-.25 11.4 11.4 0 0 0 3.6.57 1 1 0 0 1 1 1V20a1 1 0 0 1-1 1A17 17 0 0 1 3 4a1 1 0 0 1 1-1h3.5a1 1 0 0 1 1 1c0 1.250.2 2.450.57 3.57a1 1 0 0 1-.25 1z"/></svg>
      123-456-2100
    </li>
    <li>
      <svg viewBox="0 0 24 24" aria-hidden="true"><path d="M2 5h20v14H2zm2 2v.4l8 5 8-5V7zm0 2.8V17h16V9.8l-8 5z"/></svg>
      hello@cedarridgemech.com
    </li>
  </ul>

  <p class="address">Your address, city<br>state, ZIP 0000</p>

  <svg class="band-strip" viewBox="0 0 640 56" preserveAspectRatio="none" aria-hidden="true">
    <polygon points="0,0 280,0 262,12 0,12" fill="var(--strip)"/>
    <polygon points="300,0 640,0 640,56 250,56 250,34" fill="var(--band)"/>
  </svg>
  <p class="website">www.cedarridgemech.com</p>
</section>

<section class="card card--back" aria-label="Business card back">
  <div class="back-pattern" role="img" aria-label="Tone-on-tone repeating brand pattern"></div>
  <div class="back-brand">
    <span class="back-brand__square"></span>
    <span class="back-brand__name">Cedar Ridge Mechanical</span>
  </div>
</section>

</body>
</html>
```